Lawn sign for construction company

Would like this to be a very clean and high end design for luxury homes. We need a yard sign designed that includes the company logo, website, phone number and major service offerings (residential and commercial renovations and maintenance)
The company website is brackwellbuilders.com all other contact info is in the attachments
Target Market(s)
Luxury home owners and business owners
Industry/Entity Type
Construction/Home Improvement
Font styles to use
Other font styles liked:
- See company logo and other graphics included for title text fonts. All other fonts can be standard sans serif.
Colors
0054AA
0677BA
7BADD7
CADEEF
E8F1F8
Requirements
Must have
- Clean, easy to read design, would like 2 sided sign. A main sign side and back side which states “free estimates, and includes the website and phone number. Must also match the color scheme of the provided logo and other company images. Dark Navy blue primary color, gray secondary color, and orange as an accent color.
Nice to have
- 2nd sign side very simple design
Should not have
- Too many graphics limit to 1-3 colors

```html
<!DOCTYPE html>
<html lang="en">
<head>
<meta charset="utf-8">
<title>Brackwell Builders – Lawn Sign, Front and Back</title>
<link rel="stylesheet" href="https://fonts.googleapis.com/css2?family=Oswald:wght@600&family=Roboto:wght@400&family=Source+Sans+3:wght@400&display=swap">
<style>
  :root {
    --bg-light: #e8e8ea;
    --bg-dark: #d3d3d5;
    --navy: #101b37;
    --gold-deep: #b9782a;
    --gold-bright: #e8b866;
    --orange: #e8782a;
    --mark-gray: #6e6e70;
    --white: #ffffff;
    --ink: #111111;
  }
  * { margin: 0; padding: 0; box-sizing: border-box; }
  html, body { width: 1200px; height: 491px; overflow: hidden; background: var(--bg-light); }
  .board { position: relative; width: 1200px; height: 491px; overflow: hidden; }
  .board-backdrop { position: absolute; inset: 0; }
  .side-label {
    position: absolute; top: 28px; width: 493px; text-align: center;
    font-family: "Source Sans 3", sans-serif; font-weight: 400; font-size: 60px; line-height: 60px; color: var(--ink);
  }
  .sign {
    position: absolute; top: 112.5px; width: 493px; height: 323px;
    background: var(--navy); box-shadow: 0 1px 3px rgba(0,0,0,.25);
  }
  .sign--front, .label--front { left: 86.5px; }
  .sign--back, .label--back { left: 620.5px; }
  .frame-outer {
    position: absolute; left: 18px; top: 18px; right: 18px; bottom: 18px;
    border: 4px solid var(--gold-deep);
    border-image: linear-gradient(90deg, var(--gold-deep), var(--gold-bright), var(--gold-deep), var(--gold-bright), var(--gold-deep)) 1;
  }
  .frame-inner {
    position: absolute; left: 25px; top: 25px; right: 25px; bottom: 25px;
    border: 1px solid var(--gold-bright);
  }
  .company-name {
    position: absolute; left: 0; right: 0; top: 98px;
    display: flex; align-items: center; justify-content: center; gap: 10px;
    font-family: "Oswald", sans-serif; font-weight: 600; font-size: 30px; line-height: 36px;
    color: var(--orange); letter-spacing: 1px; text-transform: uppercase;
  }
  .company-dot { width: 22px; height: 22px; border-radius: 50%; background: var(--mark-gray); }
  .rule {
    position: absolute; left: 113px; width: 267px; height: 1.5px;
    background: linear-gradient(90deg, var(--gold-deep), var(--gold-bright), var(--gold-deep));
  }
  .rule--top { top: 211px; }
  .rule--bottom { top: 253px; }
  .headline {
    position: absolute; left: 0; right: 0; top: 213px; text-align: center;
    font-family: "Roboto", sans-serif; font-size: 30px; line-height: 38px; color: var(--white);
  }
  .contact {
    position: absolute; left: 0; right: 0; top: 262px; text-align: center;
    font-family: "Roboto", sans-serif; font-size: 16px; line-height: 20px; color: var(--white);
  }
  .services {
    position: absolute; left: 0; right: 0; top: 212px; list-style: none; text-align: center;
    font-family: "Oswald", sans-serif; font-weight: 600; font-size: 21px; line-height: 21px;
    color: var(--orange); letter-spacing: 5px; text-transform: uppercase;
  }
</style>
</head>
<body>
<main class="board">
  <svg class="board-backdrop" width="1200" height="491" viewBox="0 0 1200 491" aria-hidden="true">
    <rect width="1200" height="491" fill="var(--bg-light)"/>
    <polygon points="1200,0 1200,491 0,491" fill="var(--bg-dark)"/>
  </svg>

  <h2 class="side-label label--front">Front</h2>
  <h2 class="side-label label--back">Back</h2>

  <section class="sign sign--front" aria-label="Sign front">
    <div class="frame-outer"></div>
    <div class="frame-inner"></div>
    <h1 class="company-name"><span class="company-dot"></span>Brackwell Builders</h1>
    <div class="rule rule--top"></div>
    <p class="headline">FREE ESTIMATES</p>
    <div class="rule rule--bottom"></div>
    <p class="contact">brackwellbuilders.com | 555 318 204 6</p>
  </section>

  <section class="sign sign--back" aria-label="Sign back">
    <div class="frame-outer"></div>
    <div class="frame-inner"></div>
    <h1 class="company-name"><span class="company-dot"></span>Brackwell Builders</h1>
    <ul class="services">
      <li>General Contracting</li>
      <li>Property Management</li>
      <li>Remodeling</li>
    </ul>
  </section>
</main>
</body>
</html>
```